Verodex business card

Business card for sustainable investment company called "Verodex". Verodex is an exchange platform selling carbon credits between buyers and sellers. Carbon Credits are an environmental commodity for reducing global carbon emissions.

the card should obviously have our logo and the theme should be sustainability/environment mixed with a trading platform.

Contact Information for Business Card

Logo, Name, Title, Phone, Email

Colors
0054AA
0677BA
7BADD7
CADEEF
E8F1F8
0094D4
00A9DD
6FCCEA
C7EBF8
E9F6FB
00AB8E
00BBA5
67D7C9
C6EFE9
E9F9F6
59FF00
82FF00
B8FF75
E3FFCB
F4FFEA

```html
<!DOCTYPE html>
<html lang="en">
<head>
<meta charset="utf-8">
<title>Verodex business card</title>
<link rel="stylesheet" href="https://fonts.googleapis.com/css2?family=Montserrat:wght@400;500;700;800&display=swap">
<style>
  :root {
    --navy: #172a50;
    --blue: #4a86c8;
    --sky: #55a6d2;
    --aqua: #6fccea;
    --deep: #0677ba;
    --paper: #ffffff;
    --table: #1d2026;
    --ink: #1b2233;
  }
  * { box-sizing: border-box; margin: 0; padding: 0; }
  html, body { width: 1200px; height: 900px; overflow: hidden; }
  body {
    background: var(--table);
    font-family: "Montserrat", sans-serif;
    position: relative;
  }
  .card {
    position: absolute;
    left: 320px;
    width: 560px;
    height: 320px;
    border-radius: 14px;
    overflow: hidden;
  }
  .card--front { top: 100px; background: var(--paper); }
  .card--back { top: 480px; background: var(--navy); }
  .card__shapes { position: absolute; inset: 0; }
  .brand {
    position: absolute;
    display: flex;
    align-items: center;
    gap: 12px;
  }
  .brand__dot {
    width: 30px; height: 30px; border-radius: 50%;
    background: linear-gradient(135deg, var(--aqua), var(--deep));
  }
  .brand__name {
    font-weight: 800;
    letter-spacing: 1px;
    text-transform: uppercase;
  }
  .card--front .brand { left: 44px; top: 36px; }
  .card--front .brand__name { font-size: 34px; color: var(--navy); }
  .address {
    position: absolute; left: 44px; top: 96px;
    font-size: 12px; line-height: 17px; color: var(--ink);
  }
  .contacts {
    position: absolute; left: 44px; top: 140px;
    list-style: none; font-size: 12px; color: var(--ink);
  }
  .contacts li { display: flex; align-items: center; gap: 8px; height: 20px; }
  .contacts svg { width: 12px; height: 12px; fill: var(--sky); }
  .person {
    position: absolute; right: 40px; top: 150px; text-align: right;
  }
  .person__name {
    font-size: 22px; font-weight: 800; color: var(--blue); letter-spacing: 1px;
  }
  .person__title {
    font-size: 13px; font-weight: 500; color: var(--ink); letter-spacing: 2px;
  }
  .card--back .brand {
    left: 50%; top: 50%; transform: translate(-50%, -50%); gap: 18px;
  }
  .card--back .brand__dot { width: 54px; height: 54px; }
  .card--back .brand__name { font-size: 52px; color: var(--paper); }
</style>
</head>
<body>
  <section class="card card--front">
    <svg class="card__shapes" viewBox="0 0 560 320" aria-hidden="true">
      <defs>
        <linearGradient id="markFill" x1="0" y1="0" x2="1" y2="1">
          <stop offset="0" stop-color="#6fccea"/>
          <stop offset="1" stop-color="#0677ba"/>
        </linearGradient>
      </defs>
      <path d="M0,200 Q250,330 560,262 L560,320 L0,320 Z" fill="#55a6d2"/>
      <path d="M0,216 Q250,340 560,280 L560,320 L0,320 Z" fill="#ffffff"/>
      <path d="M0,222 Q250,345 560,286 L560,320 L0,320 Z" fill="#172a50"/>
      <rect x="538" y="190" width="22" height="40" fill="#55a6d2"/>
      <circle cx="420" cy="252" r="66" fill="url(#markFill)" stroke="#ffffff" stroke-width="9"/>
    </svg>

    <div class="brand">
      <span class="brand__dot"></span>
      <span class="brand__name">Verodex</span>
    </div>

    <p class="address">2271 Harbor Ridge Rd. Suite 4<br>Lakemont, OR 97455</p>

    <ul class="contacts">
      <li><svg viewBox="0 0 24 24"><path d="M6.6 10.8a15 15 0 0 0 6.6 6.6l2.2-2.2a1 1 0 0 1 1-.25 11.4 11.4 0 0 0 3.6.57 1 1 0 0 1 1 1V20a1 1 0 0 1-1 1A17 17 0 0 1 3 4a1 1 0 0 1 1-1h3.5a1 1 0 0 1 1 1c0 1.25.2 2.45.57 3.57a1 1 0 0 1-.25 1z"/></svg>541-308-7716</li>
      <li><svg viewBox="0 0 24 24"><path d="M2 5h20v14H2z M2 5l10 8 10-8" /></svg>hello@verodex.com</li>
      <li><svg viewBox="0 0 24 24"><circle cx="12" cy="12" r="10"/></svg>www.verodex.com</li>
    </ul>

    <div class="person">
      <p class="person__name">DANA ORLOV</p>
      <p class="person__title">MANAGER</p>
    </div>
  </section>

  <section class="card card--back">
    <div class="brand">
      <span class="brand__dot"></span>
      <span class="brand__name">Verodex</span>
    </div>
  </section>
</body>
</html>
```